new letterhead for my brokergae company KeelBright, Complete Marine Brokering

We need a new letterhead for our brokerage company called KeelBright. We are specialised in selling pleasure crafts (sailing and motoryachts). More info can be found at https://keelbright-example.com/en

I use this document for a quotation, a letter, sales agreement, selling instructions. I am looking for a cover page + a content page.

Th efollowing information needs to be in the header / footer; email, website, VAT number, Bank Account number, number chamber of ccomerce, registry number olpa, General terms and conditions TQRV apply.

```html
<!DOCTYPE html>
<html lang="en">
<head>
<meta charset="utf-8">
<title>KeelBright Letterhead</title>
<link href="https://fonts.googleapis.com/css2?family=Roboto:wght@400;500;700&family=Ubuntu:wght@400&family=Great+Vibes&display=swap" rel="stylesheet">
<style>
  :root {
    --backdrop: #b3b3b3;
    --paper: #f6f6f6;
    --brand-blue: #0b5aa6;
    --accent-orange: #f04b0c;
    --text-grey: #666666;
    --text-dark: #2b2b2b;
    --sign-blue: #1f4f8f;
  }
  * { margin: 0; padding: 0; box-sizing: border-box; }
  html, body {
    width: 1132px; height: 1200px; overflow: hidden;
    background: var(--backdrop);
  }
  .stage { position: relative; width: 1132px; height: 1200px; }
  .letter-page {
    position: absolute; left: 155px; top: 19px;
    width: 797px; height: 1127px;
    background: var(--paper);
    transform: scale(1.03); transform-origin: top left;
    font-family: "Roboto", Arial, sans-serif;
    color: var(--text-grey);
    overflow: hidden;
  }
  .brand { position: absolute; left: 52px; top: 88px; }
  .brand-name {
    font-family: "Roboto", Arial, sans-serif; font-weight: 500;
    font-size: 40px; line-height: 1; color: var(--brand-blue);
    display: flex; align-items: center; gap: 10px;
  }
  .brand-dot { width: 14px; height: 14px; border-radius: 50%; background: var(--brand-blue); }
  .brand-tagline {
    margin-top: 8px; margin-left: 24px;
    font-size: 10px; font-weight: 500; letter-spacing: 2.4px;
    text-transform: uppercase; color: var(--brand-blue);
  }
  .header-divider {
    position: absolute; left: 522px; top: 66px;
    width: 1.5px; height: 98px; background: var(--accent-orange);
  }
  .contact-block {
    position: absolute; left: 546px; top: 68px;
    font-family: "Ubuntu", Arial, sans-serif; font-size: 13px; font-style: normal;
    line-height: 15.5px; color: var(--text-dark);
    white-space: nowrap;
  }
  .contact-address { margin-bottom: 9px; }
  .contact-line { display: flex; align-items: center; height: 17px; }
  .contact-icon { width: 27px; flex: none; display: flex; align-items: center; padding-left: 1px; }
  .contact-icon svg { width: 11px; height: 11px; fill: var(--brand-blue); }
  .letter-body {
    position: absolute; left: 51px; top: 330px; width: 697px;
    font-size: 13px; line-height: 18px; letter-spacing: -0.15px;
  }
  .letter-date { margin-bottom: 36px; }
  .recipient-name { font-weight: 700; }
  .recipient { margin-bottom: 36px; }
  .salutation { margin-bottom: 18px; }
  .letter-body p.paragraph { text-align: justify; margin-bottom: 18px; }
  .signoff { position: absolute; left: 51px; top: 862px; font-size: 13px; line-height: 18px; }
  .signoff-name { font-weight: 700; }
  .signature {
    font-family: "Great Vibes", cursive; font-size: 30px; color: var(--sign-blue);
    margin: 8px 0 0 -16px; line-height: 36px; white-space: nowrap;
  }
  .signoff-role { margin-top: 10px; }
  .footer-band {
    position: absolute; left: 0; top: 1081px; width: 100%; height: 11px;
    background: var(--accent-orange);
  }
  .footer-brand {
    position: absolute; left: 640px; top: 1075px;
    padding: 0 8px; background: var(--paper);
    font-weight: 500; font-size: 18px; line-height: 22px; color: var(--brand-blue);
  }
  .footer-details {
    position: absolute; left: 51px; top: 1102px; width: 580px;
    font-size: 8.5px; line-height: 11px; color: var(--text-grey);
    white-space: nowrap;
  }
</style>
</head>
<body>
<div class="stage">
  <div class="letter-page">
    <header>
      <div class="brand">
        <div class="brand-name"><span class="brand-dot"></span>KeelBright</div>
        <div class="brand-tagline">Complete Marine Brokering</div>
      </div>
      <div class="header-divider"></div>
      <address class="contact-block">
        <div class="contact-address">Havenkade 12, 3011 AB<br>Rotterdam, Netherland</div>
        <div class="contact-line">
          <span class="contact-icon"><svg viewBox="0 0 12 12"><path d="M2 1h3l1 3-1.5 1a7 7 0 0 0 2.5 2.5L8 6l3 1v3c0 .6-.4 1-1 1A9 9 0 0 1 1 2c0-.6.4-1 1-1z"/></svg></span>
          <span>+31 (0)20 555 01 23</span>
        </div>
        <div class="contact-line">
          <span class="contact-icon"><svg viewBox="0 0 12 12"><path d="M1 2.5h10v7H1z M1.5 3 6 6.5 10.5 3" fill="none" stroke="#0b5aa6" stroke-width="1.3"/></svg></span>
          <span>contact@keelbright-example.com</span>
        </div>
        <div class="contact-line">
          <span class="contact-icon"><svg viewBox="0 0 12 12"><circle cx="6" cy="6" r="4.8" fill="none" stroke="#0b5aa6" stroke-width="1.2"/><path d="M1.2 6h9.6M6 1.2v9.6" stroke="#0b5aa6" stroke-width="1"/><ellipse cx="6" cy="6" rx="2.2" ry="4.8" fill="none" stroke="#0b5aa6" stroke-width="1"/></svg></span>
          <span>www.keelbright-example.com</span>
        </div>
      </address>
    </header>

    <main class="letter-body">
      <div class="letter-date">30/20/2016</div>
      <div class="recipient">
        <div class="recipient-name">Mr. XYZ Smith</div>
        <div>123, Street No. 123,</div>
        <div>City Name</div>
        <div>Pincode-123456</div>
      </div>
      <div class="salutation">Dear Sir,</div>
      <p class="paragraph">Lorem Ipsum is simply dummy text of the printing and typesetting industry. Lorem Ipsum has been the industry's standard dummy text ever since the 1500s, when an unknown printer took a galley of type and scrambled it to make a type specimen book. It has survived not only five centuries, but also the leap into electronic typesetting, remaining essentially unchanged. It was popularised in the 1960s with the release of Letraset sheets containing Lorem Ipsum passages, and more recently with desktop publishing software like Aldus PageMaker including versions of Lorem Ipsum.</p>
      <p class="paragraph">Lorem Ipsum is simply dummy text of the printing and typesetting industry. Lorem Ipsum has been the industry's standard dummy text ever since the 1500s, when an unknown printer took a galley of type and scrambled it to make a type specimen book. It has survived not only five centuries, but also the leap into electronic typesetting, remaining essentially unchanged. It was popularised in the 1960s with the release of Letraset sheets containing Lorem Ipsum passages, and more recently with desktop publishing software like Aldus PageMaker including versions of Lorem Ipsum.</p>
      <p class="paragraph">Lorem Ipsum is simply dummy text of the printing and typesetting industry. Lorem Ipsum has been the industry's standard dummy text ever since the 1500s, when an unknown printer took a galley of type and scrambled it to make a type specimen book.</p>
    </main>

    <section class="signoff">
      <div class="signoff-name">Your Name</div>
      <div class="signature">Your Signature</div>
      <div class="signoff-role">CEO &nbsp;|&nbsp; Owner</div>
    </section>

    <footer>
      <div class="footer-band"></div>
      <div class="footer-brand">KeelBright</div>
      <div class="footer-details">
        <div>VAT NL000000000B01 &nbsp;|&nbsp; IBAN NL00 BANK 0000 0000 00 &nbsp;|&nbsp; Chamber of Commerce 00000000 &nbsp;|&nbsp; olpa reg. 0000</div>
        <div>General terms and conditions TQRV apply</div>
      </div>
    </footer>
  </div>
</div>
</body>
</html>
```